San Francisco Leading Consulting firm - 47Vora Web Design Project

•Create a Web Design
•Uncoded webpage layout design
•2 Pages Design - Homepage + Interior Page

Task Description
Hello, we're looking for a re-design our current website www.47vora-example.com

we have a sample mockup design @

http://47vora.pubtrellis-example.org/

This shows the layout that we like and also a sample of 6 pictures that would change based on where you mouse over..

6 pictures HOME design needs to be included.

SMART
THOUGHTFUL
FLEXIBLE
CREATIVE SERVICES
TECHNICAL SERVICES
PARTNERS

sites we like:

http://www.melvanadvisory-example.com/Home.cfm?id=Home
http://www.plinthworks-example.com/index.html

Our company can be best described as: 100+ employees, cutting-edge, depandable, innovative, strong, smart.

Our Primary focus is: IT Consulting Services and Creative Design services

47Vora LLC is a consulting firm providing creative design, business and technology solutions to both private and public interests.

Established in 1996, 47Vora is a San Francisco based company providing specialists for a range of business needs including:

Creative Design Services
•Print
•Logo Design
•Website Design
•Illustration

and

Business and Technology solutions

•Application Software and Web Development
•Business Process Re-Design (BPR)
•Business/Systems Analysis and Requirement Documentation
•Mentoring and Training
•Network/Hardware Installation Services
•System Design and Architecture
•Vendor Management
•Docuvault Architecture and Implementation

our sample mockup site:

Reason: Due to holiday season, we're not available to work with designers and finilize our design.  

Thank you very much for submitting your design.

We appreciate your time and creativity.   Since, our office is currently closed for holidays, we will be reviewing it in details next week and will make our decision as soon as possible.

It would be great if you could submit any of your changes by Wed next week, so it would be part of our reviews. 

Please see updated wireframe under attachments:  we have some minor updates to our wireframe that we would like you to update your designs, if possible.  

We also encorouge you not to use our standard wireframe and come up with more unique designs.   Everything would be considered when we review your design.

 

Target Market(s)

Creative services and professional services clients, including government agencies

Industry/Entity Type

Business

Requirements
Must have
• Clean, professional look, easy navigation

```html
<!DOCTYPE html>
<html lang="en">
<head>
<meta charset="utf-8">
<title>47Vora – Technology Solutions for the 21st Century</title>
<link rel="stylesheet" href="https://fonts.googleapis.com/css2?family=Open+Sans:ital,wght@0,400;0,600;0,700;1,400&display=swap">
<style>
:root{
  --header-bg:#eef6fa;
  --nav-bg:#dcebf3;
  --brand-blue:#1c8fc9;
  --cyan:#2fd0e6;
  --teal-dark:#17b4cf;
  --text:#333a40;
  --muted:#666d73;
  --link:#2275b8;
  --accent-orange:#f0a020;
  --page-bottom:#fbfcfd;
  --rule:#d8dde1;
}
*{box-sizing:border-box;margin:0;padding:0}
html,body{width:1159px;height:1200px;overflow:hidden}
body{
  position:relative;
  font-family:"Open Sans",Arial,sans-serif;
  color:var(--text);
  background:linear-gradient(to bottom,#fff 0,#fff 300px,#dfe3e7 300px,#eceef0 620px,#e6e9ec 640px,var(--page-bottom) 900px,#fff 1200px);
}
.abs{position:absolute}

/* header */
.site-header{left:0;top:0;width:1159px;height:100px;background:var(--header-bg)}
.brand{left:147px;top:38px;display:flex;align-items:center;gap:9px}
.brand-mark{width:22px;height:22px;background:var(--brand-blue)}
.brand-name{font-size:27px;font-weight:400;color:#3b4650;letter-spacing:1px}
.tagline{left:333px;top:50px;font-size:12.5px;color:#3b4650}
.contact{left:923px;top:16px;font-size:11.5px;color:#6c757c;line-height:1.3}
.contact .big{font-size:16px;color:var(--brand-blue);display:block;margin-bottom:6px}
.contact .mail{font-size:12.5px;color:var(--brand-blue);display:block}

/* nav */
.main-nav{left:0;top:100px;width:1159px;height:37px;background:var(--nav-bg)}
.nav-item{position:absolute;top:12px;font-size:11px;font-weight:700;letter-spacing:.8px;color:#2f3840}
.nav-item .chev{color:var(--accent-orange);margin-left:9px;font-weight:700}
.search{left:872px;top:108px;width:149px;height:21px;background:#fff;border:1px solid #cfdde6;border-radius:2px;font-size:8px;font-style:italic;color:#9aa3aa;padding:5px 7px}
.search svg{position:absolute;right:4px;top:3px}

/* welcome */
.welcome-title{left:152px;top:165px;font-size:37px;font-weight:400;color:var(--cyan);line-height:1}
.welcome-text{left:151px;top:225px;width:870px;font-size:12px;line-height:1.15}
.welcome-text p{margin-bottom:19px}

/* slider */
.slider{left:137px;top:300px;width:880px;height:311px;background:linear-gradient(160deg,#4fe9ee 0%,var(--cyan) 40%,var(--teal-dark) 100%)}
.slide-photo{left:363px;top:0;width:437px;height:311px;background:radial-gradient(ellipse at 50% 45%,#d9b59c 0%,#c99b80 35%,#b8b9b0 75%,#9ea39a 100%)}
.slide-title{left:62px;top:125px;font-size:46px;font-weight:400;color:#fff;line-height:1}
.slide-sub{left:63px;top:196px;font-size:19.5px;font-weight:400;color:#fff;line-height:1.25}
.slide-arrow{top:140px}
.slide-dots{left:18px;top:292px;display:flex;gap:5px}
.slide-dots span{width:6px;height:6px;border-radius:50%;background:rgba(255,255,255,.45)}
.slide-dots span:first-child{background:#fff}

/* service cards */
.card{top:648px;width:256px;height:147px;background:linear-gradient(#fff,#f4f5f6);border-radius:9px;box-shadow:0 2px 5px rgba(0,0,0,.12)}
.card-reflection{top:797px;width:256px;height:50px;border-radius:9px;background:linear-gradient(rgba(255,255,255,.7),rgba(255,255,255,0))}
.card svg{position:absolute;left:22px;top:38px}
.card-title{position:absolute;left:76px;top:44px;font-size:17.5px;font-weight:400;line-height:1.2;color:#2c3338;white-space:nowrap}
.card-title span{display:block;color:var(--muted)}
.card-more{position:absolute;right:18px;top:117px;font-size:11.5px;color:#3d454b}
.card-more b{color:var(--accent-orange);font-weight:700;margin-left:4px}

/* clients & testimonial */
.clients{left:144px;top:865px;width:584px;height:86px;background:#fff;border:1px solid #d3d8dc;border-radius:9px;font-size:16px;color:var(--muted);padding:29px 15px}
.clients svg{position:absolute;right:10px;top:33px}
.testimonial{left:760px;top:862px;width:235px}
.testimonial h3{font-size:15.5px;font-weight:400;color:#5a6167}
.testimonial blockquote{font-size:10.5px;font-style:italic;color:#6a7278;line-height:1.3;margin-top:18px}
.testimonial cite{display:block;text-align:right;font-size:9px;font-style:normal;color:#6a7278;margin-top:8px}
.quote-mark{font-size:30px;color:#8ed3e8;line-height:1;font-family:Georgia,serif}

/* service lists */
.services h4{font-size:12.5px;font-weight:700;color:#2f363b}
.services ul{list-style:none;margin-top:16px}
.services li{font-family:Arial,sans-serif;font-size:10px;color:var(--link);line-height:1.25;margin-bottom:12.2px;padding-left:16px;text-indent:-8px}
.services li::before{content:"•";margin-right:4px}
.divider{left:412px;top:977px;width:1px;height:160px;background:var(--rule)}

/* footer */
.site-footer{left:96px;top:1155px;width:917px;height:45px;border-top:1px solid #e1e5e8;background:linear-gradient(#f1f3f5,#fff 30%);font-family:Arial,sans-serif;font-size:10px;text-align:center;padding-top:17px;color:#222}
</style>
</head>
<body>

<header class="site-header abs">
  <div class="brand abs"><span class="brand-mark"></span><span class="brand-name">47Vora</span></div>
  <p class="tagline abs">Thechnology Solutions for the 21st Century</p>
  <div class="contact abs">
    Call us at<span class="big">800.555.0146</span>
    Email us at<span class="mail">info@47vora-example.com</span>
  </div>
</header>

<nav class="main-nav abs">
  <span class="nav-item" style="left:151px">COMPANY<span class="chev">›</span></span>
  <span class="nav-item" style="left:248px">CREATIVE SERVICES<span class="chev">›</span></span>
  <span class="nav-item" style="left:407px">TECHNICAL SERVICES<span class="chev">›</span></span>
  <span class="nav-item" style="left:584px">PARTNERS<span class="chev">›</span></span>
  <span class="nav-item" style="left:695px">CONTACT US</span>
</nav>
<div class="search abs">SEARCH
  <svg width="14" height="14" viewBox="0 0 14 14"><circle cx="8" cy="6" r="4" fill="none" stroke="#f0a020" stroke-width="1.6"/><line x1="5" y1="9" x2="1.5" y2="12.5" stroke="#f0a020" stroke-width="1.8"/></svg>
</div>

<h1 class="welcome-title abs">welcome</h1>
<div class="welcome-text abs">
  <p>47Vora LLC is a consulting firm providing creative design, business and technology solutions to both private and public interests.</p>
  <p>Our experts possess broad industry knowledge which can help with technical and businessprocess challenges, delivering solutions that are creative and cost effective.</p>
</div>

<section class="slider abs">
  <div class="slide-photo abs" role="img" aria-label="Photo of two hands holding a floating puzzle cube"></div>
  <svg class="slide-arrow abs" style="left:16px" width="14" height="34" viewBox="0 0 14 34"><polyline points="12,2 2,17 12,32" fill="none" stroke="#fff" stroke-width="2"/></svg>
  <svg class="slide-arrow abs" style="left:850px" width="14" height="34" viewBox="0 0 14 34"><polyline points="2,2 12,17 2,32" fill="none" stroke="#fff" stroke-width="2"/></svg>
  <h2 class="slide-title abs">smart</h2>
  <p class="slide-sub abs">We don't believe in term of<br>"overqualified"</p>
  <div class="slide-dots abs"><span></span><span></span><span></span><span></span><span></span><span></span></div>
</section>

<article class="card abs" style="left:145px">
  <svg width="46" height="50" viewBox="0 0 46 50"><polygon points="4,46 42,46 4,8" fill="none" stroke="#1c8fc9" stroke-width="4"/><polygon points="12,38 26,38 12,24" fill="none" stroke="#1c8fc9" stroke-width="3"/><polygon points="30,2 38,8 14,40 6,42 8,34" fill="#1c8fc9"/></svg>
  <h3 class="card-title">Creative<span>Services</span></h3>
  <a class="card-more">Lean More<b>›</b></a>
</article>
<div class="card-reflection abs" style="left:145px"></div>

<article class="card abs" style="left:449px">
  <svg width="46" height="50" viewBox="0 0 46 50"><path d="M4 40 L26 16 A9 9 0 1 1 34 22 L12 46 Z" fill="#9b3c44"/><polygon points="26,30 36,30 31,24" fill="#9b3c44"/><rect x="29" y="30" width="4" height="16" fill="#9b3c44"/></svg>
  <h3 class="card-title" style="left:72px;font-size:17px">Business &amp; Technical<span>Services</span></h3>
  <a class="card-more">Lean More<b>›</b></a>
</article>
<div class="card-reflection abs" style="left:449px"></div>

<article class="card abs" style="left:753px">
  <svg width="50" height="46" viewBox="0 0 50 46"><polygon points="2,10 12,4 20,14 10,20" fill="#8fb339"/><polygon points="48,10 38,4 30,14 40,20" fill="#8fb339"/><path d="M12 16 L24 10 L36 18 L28 34 L20 36 L10 24 Z" fill="#8fb339"/></svg>
  <h3 class="card-title" style="top:54px">Partners</h3>
  <a class="card-more">Lean More<b>›</b></a>
</article>
<div class="card-reflection abs" style="left:753px"></div>

<section class="clients abs">Our Clinets
  <svg width="10" height="16" viewBox="0 0 10 16"><polyline points="2,2 8,8 2,14" fill="none" stroke="#777" stroke-width="2"/></svg>
</section>

<aside class="testimonial abs">
  <h3>Testimonials</h3>
  <div class="quote-mark" style="position:absolute;top:20px">“</div>
  <blockquote>Lorem ipsum dolor sit amet, consectetuer adiping elit, sed diam nonummy nibh euismod.
    <cite>Dana Morel, CEO of Company</cite>
  </blockquote>
  <div class="quote-mark" style="text-align:right">”</div>
</aside>

<section class="services abs" style="left:146px;top:989px">
  <h4>Creative Design Services</h4>
  <ul style="margin-left:12px">
    <li>Print</li><li>Logo Design</li><li>Website Design</li><li>Illustration</li>
  </ul>
</section>
<div class="divider abs"></div>
<section class="services abs" style="left:459px;top:989px;width:560px">
  <h4>Business and Technical solutions</h4>
  <ul style="position:absolute;left:13px;top:18px;width:250px">
    <li>Application Software and Web Development</li>
    <li>Business Process Re-Design (BPR)</li>
    <li>Business/Systems Analysis and Requirement Documentation</li>
    <li>Mentoring and Training</li>
  </ul>
  <ul style="position:absolute;left:272px;top:18px;width:260px">
    <li>Network/Hardware Installation Services</li>
    <li>System Design and Architecture</li>
    <li>Vendor Management</li>
    <li>Docuvault Architecture and Implementation</li>
  </ul>
</section>

<footer class="site-footer abs">Copyright 2010, 47Vora, LLC All rights reserved.</footer>

</body>
</html>
```